Meadow Kr Circle (company name is Meadow Kr Circle LLP)

management of homestay, hospitality something similar with https://www.dorvika.example

Target Market(s)

johor bahru market (Malaysia)

Contact Information for Business Card

Meadow Circle KR LLP

Logo Text

eyes catching, attractive, amazing, Nice, jaw dropping for design

Coding

Coded - Design and coding required

Number of Pages Required

5+ page

Colors

Designer to choose colors to be used in the design.

Requirements
Must have
• please change the short term proposal to our company logo and change the name from dorvika to meadow KR Circle LLP
• thanks
Nice to have
• please let me have eyes catching , jaw dropping design

```html
<!DOCTYPE html>
<html lang="en">
<head>
<meta charset="utf-8">
<title>Meadow Kr Circle — Homestay Management</title>
<link href="https://fonts.googleapis.com/css2?family=Lato:wght@400;700;900&family=Oswald:wght@400;500&display=swap" rel="stylesheet">
<style>
:root{
  --blue:#1a3ec0;
  --blue-deep:#1538b8;
  --sky:#cde6f3;
  --step:#d3e9f6;
  --step-text:#5d7fbf;
  --ink:#1d2233;
  --body:#4a4f5c;
  --footer:#0c1a44;
  --social:#d5e6f2;
  --white:#fff;
}
*{margin:0;padding:0;box-sizing:border-box}
html,body{width:1200px;height:3774px;overflow:hidden}
body{font-family:'Lato',sans-serif;color:var(--ink);background:var(--white);position:relative}
.abs{position:absolute}
.btn{position:absolute;background:var(--blue);color:var(--white);font-size:12px;font-weight:700;letter-spacing:.5px;display:flex;align-items:center;justify-content:center;text-transform:uppercase}
.section-title{position:absolute;left:145px;font-size:24px;font-weight:400;color:var(--blue);text-transform:uppercase;padding-bottom:6px;border-bottom:3px solid var(--blue)}
.para{position:absolute;font-size:13px;line-height:19px;color:var(--body)}

/* hero */
.hero{position:absolute;left:0;top:0;width:1200px;height:616px;background:linear-gradient(160deg,#3a5cc4 0%,#2446ad 55%,#1f3f9f 100%)}
.logo{position:absolute;left:145px;top:22px;font-size:38px;color:var(--white);font-weight:400}
.nav{position:absolute;top:38px;right:145px;display:flex;gap:40px;font-size:14px;color:var(--white)}
.nav .active{text-decoration:underline;text-underline-offset:5px}
.hero-title{position:absolute;left:0;width:1200px;top:262px;text-align:center;font-size:34px;line-height:42px;color:var(--white);font-weight:400}
.hero-btn{position:absolute;left:540px;top:360px;width:120px;height:44px;border:2px solid var(--white);color:var(--white);font-size:12px;display:flex;align-items:center;justify-content:center}
.scroll-down{position:absolute;left:545px;top:560px;width:110px;height:110px;border-radius:50%;background:var(--white)}

/* about */
.about{position:absolute;top:616px;left:0;width:1200px;height:354px;background:var(--sky)}
.about-heading{position:absolute;left:145px;top:138px;width:340px;font-size:40px;line-height:46px;font-weight:700;color:var(--ink)}

/* steps */
.step{position:absolute;left:145px;width:318px;background:var(--step);color:var(--step-text);display:flex;align-items:center;gap:18px;padding-left:12px}
.step .num{font-family:'Oswald',sans-serif;font-size:54px;line-height:1}
.step .label{font-size:15px;line-height:18px}
.step.active{left:160px;background:var(--blue);color:var(--white)}
.arrow-badge{position:absolute;width:32px;height:32px;border-radius:50%;border:2px solid var(--white);background:var(--blue)}
.item-slot{position:absolute;top:1420px;width:102px;height:104px;border-right:1px solid #d7dbe3;display:flex;align-items:center;justify-content:center}
.item-slot span{width:48px;height:48px;background:#eef1f6;border:1px solid #d3d9e4}

/* testimonial */
.photo{position:absolute;left:0;top:1605px;width:1200px;height:603px;background:linear-gradient(100deg,#e4e7ea 0%,#cfd6dc 45%,#dde2e6 100%)}
.quote-box{position:absolute;left:600px;top:1932px;width:455px;height:364px;background:var(--blue);color:var(--white);text-align:center}
.quote-mark{font-family:'Oswald',sans-serif;font-size:90px;line-height:90px;margin-top:18px}
.quote-text{font-size:16px;line-height:25px;padding:0 36px;margin-top:-2px}
.quote-name{font-size:15px;font-weight:900;margin-top:14px}
.pager{display:flex;gap:6px;justify-content:center;margin-top:24px}
.pager span{width:20px;height:20px;border:1px solid var(--white);font-size:11px;display:flex;align-items:center;justify-content:center}

/* packages */
.pkg{position:absolute;left:145px;width:320px;background:var(--step);color:var(--step-text);font-size:18px;padding-left:16px;display:flex;align-items:center}
.pkg.active{left:160px;width:335px;background:var(--blue);color:var(--white);font-size:19px}
.price{position:absolute;left:598px;top:2428px;font-family:'Oswald',sans-serif;font-size:58px;font-weight:500;color:var(--blue)}
.terms{position:absolute;left:875px;top:2476px;font-size:10px;color:var(--body)}
.features{position:absolute;left:600px;top:2525px;list-style:none;font-size:18px;line-height:48px;color:var(--ink)}
.features li::before{content:"";display:inline-block;width:7px;height:7px;border-radius:50%;background:var(--ink);margin-right:14px;vertical-align:middle}

/* notes */
.notes{position:absolute;left:0;top:3060px;width:1200px;height:400px;background:var(--blue-deep);color:var(--white);text-align:center}
.notes h2{display:inline-block;margin-top:72px;font-size:23px;font-weight:700;padding-bottom:6px;border-bottom:3px solid var(--white)}
.notes p{font-size:19px;line-height:48px}
.notes .list{margin-top:18px}

/* contact */
.contact-head{position:absolute;left:145px;top:3486px;display:flex;align-items:baseline;gap:14px;color:var(--blue)}
.person{font-size:46px;font-weight:400;line-height:60px;white-space:nowrap}
.role{font-size:19px;white-space:nowrap}
.lines{position:absolute;left:145px;top:3552px;font-size:19px;color:var(--ink);display:flex;align-items:center;gap:10px}
.social{position:absolute;top:3497px;width:78px;height:78px;background:var(--social)}
.divider{position:absolute;left:145px;top:3605px;width:910px;height:1px;background:#cfd4dc}
.address{position:absolute;left:145px;top:3625px;font-size:28px;color:var(--ink)}

.footer{position:absolute;left:0;top:3693px;width:1200px;height:81px;background:var(--footer);color:#b6bdd3;font-size:11px}
.footer .links{position:absolute;left:145px;top:35px;display:flex;gap:10px}
.footer .copy{position:absolute;right:145px;top:35px}
</style>
</head>
<body>

<header class="hero" role="img" aria-label="Photo of a bright shared workspace with people at tables, tinted blue">
  <div class="logo">Meadow Kr Circle</div>
  <nav class="nav"><span class="active">About</span><span>How to start</span><span>Packages</span><span>Reviews</span><span>Contact</span></nav>
  <h1 class="hero-title">Pellentesque vehicula nulla<br>molestie lectus</h1>
  <div class="hero-btn">CONTACT US</div>
  <div class="scroll-down">
    <svg class="abs" style="left:43px;top:22px" width="24" height="16" viewBox="0 0 24 16"><path d="M4 4 L12 12 L20 4" fill="none" stroke="#1d2233" stroke-width="4"/></svg>
  </div>
</header>

<section class="about">
  <h2 class="section-title" style="top:78px">About us</h2>
  <div class="about-heading">Aenean facilisis tincidunt lectu dictum nisi</div>
  <p class="para" style="left:545px;top:78px;width:510px">Fusce nec leo ac urna pulvinar auctor. Mauris bibendum fringilla velit. Nulla in lorem at massa pellentesque posuere. Nulla tristique posuere molestie. Aliquam erat volutpat. Etiam quis aliquet risus. Duis ornare erat eget magna dapibus, in accumsan quam pharetra. Nam tempus, quam in bibendum vulputate, sapien dolor viverra nisl, vitae euismod elit turpis et nulla. Aliquam erat volutpat. Pellentesque blandit lacus eget nunc faucibus, et tincidunt eros viverra.</p>
  <div class="btn" style="left:545px;top:234px;width:112px;height:38px">Read more</div>
</section>

<section>
  <h2 class="section-title" style="top:1040px">How to start</h2>
  <p class="para" style="left:145px;top:1110px;width:290px;font-size:12px;line-height:17px">The following steps are required in order to get your place ready to start.</p>

  <div class="step active" style="top:1183px;height:79px"><span class="num">01</span><span class="label">Getting the required items</span></div>
  <div class="arrow-badge" style="left:464px;top:1206px">
    <svg width="28" height="28" viewBox="0 0 28 28"><path d="M11 8 L17 14 L11 20" fill="none" stroke="#fff" stroke-width="3"/></svg>
  </div>
  <div class="step" style="top:1272px;height:78px"><span class="num">02</span><span class="label">Renovation &amp; Furnishing</span></div>
  <div class="step" style="top:1360px;height:76px"><span class="num">03</span><span class="label">Sign a management<br>agreement</span></div>
  <div class="step" style="top:1446px;height:80px"><span class="num">04</span><span class="label">Handover Keys &amp; Access<br>cards, and relevant<br>information</span></div>

  <p class="para" style="left:545px;top:1175px;width:510px">Fusce nec leo ac urna pulvinar auctor. Mauris bibendum fringilla velit. Nulla in lorem at massa pellentesque posuere. Nulla tristique posuere molestie. Aliquam erat volutpat. Etiam quis aliquet risus. Duis ornare erat eget magna dapibus, in accumsan quam pharetra. Nam tempus, quam in bibendum vulputate, sapien dolor viverra nisl, vitae euismod elit turpis et nulla. Aliquam erat volutpat. Pellentesque blandit lacus eget nunc faucibus, et tincidunt eros viverra.</p>
  <div class="btn" style="left:545px;top:1334px;width:128px;height:38px">Choose items</div>

  <div class="item-slot" style="left:545px" role="img" aria-label="Desk icon"><span></span></div>
  <div class="item-slot" style="left:647px" role="img" aria-label="Lamp icon"><span></span></div>
  <div class="item-slot" style="left:749px" role="img" aria-label="Cabinet icon"><span></span></div>
  <div class="item-slot" style="left:851px" role="img" aria-label="Chair icon"><span></span></div>
  <div class="item-slot" style="left:953px;border-right:none" role="img" aria-label="Sofa icon"><span></span></div>
  <div class="abs" style="left:545px;top:1524px;width:510px;height:1px;background:#d7dbe3"></div>
</section>

<section>
  <div class="photo" role="img" aria-label="Photo of a bright office with colleagues meeting and a smiling client portrait"></div>
  <div class="quote-box">
    <div class="quote-mark">“</div>
    <p class="quote-text">Etiam mattis augue vehicula odio posuere, sit amet tempus lectus luctus. Nulla facilisi. Etiam vel massa elementum, bibendum tellus venenatis, feugiat massa. Curabitur venenatis lacinia ornare.</p>
    <div class="quote-name">EMILY, COMPANY NAME</div>
    <div class="pager"><span>‹</span><span>›</span></div>
  </div>
</section>

<section>
  <h2 class="section-title" style="top:2368px">Packages</h2>
  <div class="pkg active" style="top:2442px;height:62px">Economic Package</div>
  <div class="arrow-badge" style="left:464px;top:2457px">
    <svg width="28" height="28" viewBox="0 0 28 28"><path d="M11 8 L17 14 L11 20" fill="none" stroke="#fff" stroke-width="3"/></svg>
  </div>
  <div class="pkg" style="top:2516px;height:60px">Simplicity Package</div>
  <div class="pkg" style="top:2588px;height:60px">F.O.C</div>
  <div class="pkg" style="top:2660px;height:60px">Furniture Package</div>
  <div class="pkg" style="top:2732px;height:60px">Curtain, Soft touch &amp; MISC</div>
  <div class="pkg" style="top:2804px;height:60px">Electrical Appliances Package</div>
  <div class="pkg" style="top:2876px;height:104px;line-height:24px">Simplicity Reno + Furnitures +<br>Electrical Appliances +<br>Curtain, Soft touch &amp; MISC</div>

  <div class="price">RM7,950.00</div>
  <div class="terms">(*TERMS AND CONDITIONS APPLY)</div>
  <ul class="features">
    <li>Full Height Day &amp; Night curtain</li>
    <li>Main Entrance Door Grill</li>
    <li>Supply &amp; Install LED Surface Light</li>
    <li>Supply &amp; Install Down Light</li>
    <li>Supply &amp; Install Ceiling Fan</li>
    <li>Retractive Hanging Rack</li>
  </ul>
  <div class="btn" style="left:598px;top:2828px;width:106px;height:40px">Book now</div>
</section>

<section class="notes">
  <h2>THINGS TO TAKE NOTE</h2>
  <div class="list">
    <p>Interior design &amp; Furnishing of the house play an important role to guest’s booking decision.</p>
    <p>All rate shown in later projected income are not include cleaning fees.</p>
    <p>Cleaning fee will be charge extra to guests on Stayora at RM40 per booking.</p>
    <p>Meadow Kr Circle takes 30% profit sharing, whereas property owner takes 70%.</p>
  </div>
</section>

<section>
  <div class="contact-head">
    <div class="person">LIAM HARROW</div>
    <div class="role">Marketing &amp; Operations Manager</div>
  </div>
  <div class="lines">
    <svg width="18" height="18" viewBox="0 0 24 24"><path d="M6.6 10.8a15 15 0 0 0 6.6 6.6l2.2-2.2a1 1 0 0 1 1-.25 11 11 0 0 0 3.6.6 1 1 0 0 1 1 1V20a1 1 0 0 1-1 1A17 17 0 0 1 3 4a1 1 0 0 1 1-1h3.5a1 1 0 0 1 1 1c0 1.25.2 2.45.6 3.6a1 1 0 0 1-.25 1z" fill="#1d2233"/></svg>
    <span>+456 870 2291</span><span>&nbsp;|&nbsp;</span>
    <svg width="20" height="16" viewBox="0 0 20 16"><rect x="1" y="1" width="18" height="14" fill="#1d2233"/><path d="M1 1 L10 9 L19 1" fill="none" stroke="#fff" stroke-width="1.5"/></svg>
    <span>hello@meadowkrcircle.example</span>
  </div>
  <div class="social" style="left:885px" role="img" aria-label="Social profile link"></div>
  <div class="social" style="left:977px" role="img" aria-label="Social profile link"></div>
  <div class="divider"></div>
  <div class="address">L12-04 Cedar Residence, Jalan Seroja, Taman Anggerik, 80350 Johor Bahru.</div>
</section>

<footer class="footer">
  <div class="links"><span>Home</span><span>|</span><span>About</span><span>|</span><span>How to start</span><span>|</span><span>Packages</span><span>|</span><span>Reviews</span><span>|</span><span>Contact</span></div>
  <div class="copy">Copyright © 2018 Meadow Kr Circle. All rights reserved.</div>
</footer>

</body>
</html>
```